Energy Company needs a Business Card Design

We need a business card design for a new company based in Singapore called Tavren Energy. Tavren Energy is a producer of renewable energies largely for the biofuels market. Sourced entirely from sustainable resources, Tavren Energy aims to be a fully integrated oil company operating in 100% sustainable way. We would like to see designs that use the same colours as the attached file.

Industry/Entity Type

Business

```html
<!DOCTYPE html>
<html lang="en">
<head>
<meta charset="utf-8">
<title>Tavren Energy – Business Card</title>
<link rel="stylesheet" href="https://fonts.googleapis.com/css2?family=Mulish:wght@700&family=Questrial&display=swap">
<style>
  :root {
    --backdrop: #ebebeb;
    --card-light: #ffffff;
    --card-dark: #3a3b3c;
    --card-dark-edge: #2c2d2e;
    --brand-grey: #8e8e8e;
    --brand-green: #7ab338;
    --text-light: #c9c9c9;
    --shadow: rgba(0, 0, 0, 0.28);
  }
  * { margin: 0; padding: 0; box-sizing: border-box; }
  html, body {
    width: 1200px;
    height: 720px;
    overflow: hidden;
    background: var(--backdrop);
    font-family: "Questrial", "Century Gothic", sans-serif;
  }
  .stage {
    position: relative;
    width: 1200px;
    height: 720px;
  }
  .card {
    position: absolute;
    top: 241px;
    width: 420px;
    height: 240px;
    box-shadow: -6px 14px 22px var(--shadow);
  }
  .card--front {
    left: 147px;
    background: var(--card-light);
  }
  .card--back {
    left: 633px;
    background: linear-gradient(135deg, #4a4b4c 0%, var(--card-dark) 45%, var(--card-dark-edge) 100%);
  }

  /* Front */
  .front-brand {
    position: absolute;
    top: 52px;
    left: 0;
    width: 100%;
    display: flex;
    justify-content: center;
    align-items: center;
    gap: 10px;
  }
  .brand-name {
    color: var(--brand-grey);
    font-family: "Questrial", "Century Gothic", sans-serif;
    font-weight: 400;
    line-height: 1;
  }
  .front-brand .brand-name { font-size: 76px; letter-spacing: -1px; }
  .brand-dot {
    display: block;
    border-radius: 50%;
    background: var(--brand-green);
  }
  .front-brand .brand-dot { width: 18px; height: 18px; }
  .tagline {
    position: absolute;
    top: 182px;
    left: 0;
    width: 100%;
    text-align: center;
    color: var(--brand-green);
    font-size: 15px;
  }

  /* Back */
  .contact {
    position: absolute;
    left: 21px;
    top: 66px;
  }
  .contact-name {
    font-family: "Mulish", "Century Gothic", sans-serif;
    font-weight: 700;
    font-size: 15px;
    color: var(--brand-green);
    line-height: 1.1;
  }
  .contact-role {
    font-size: 13px;
    color: var(--text-light);
    line-height: 1.2;
  }
  .contact-list {
    list-style: none;
    margin-top: 26px;
  }
  .contact-list li {
    display: flex;
    align-items: center;
    gap: 7px;
    height: 19.5px;
    font-size: 11px;
    color: var(--text-light);
  }
  .contact-list svg { width: 10px; height: 10px; flex: none; }
  .back-brand {
    position: absolute;
    right: 24px;
    top: 96px;
    display: flex;
    align-items: center;
    gap: 7px;
  }
  .back-brand .brand-name { font-size: 28px; color: #9a9a9a; }
  .back-brand .brand-dot { width: 10px; height: 10px; }
</style>
</head>
<body>
<main class="stage">
  <section class="card card--front" aria-label="Card front">
    <div class="front-brand">
      <span class="brand-dot"></span>
      <span class="brand-name">Tavren</span>
    </div>
    <p class="tagline">Energy for Biofuels Market</p>
  </section>

  <section class="card card--back" aria-label="Card back">
    <div class="contact">
      <p class="contact-name">Marcus Lindqvist</p>
      <p class="contact-role">CEO</p>
      <ul class="contact-list">
        <li>
          <svg viewBox="0 0 10 10" aria-hidden="true"><rect x="2.5" y="0.5" width="5" height="9" rx="1" fill="none" stroke="#7ab338" stroke-width="1"/><line x1="4.3" y1="8" x2="5.7" y2="8" stroke="#7ab338" stroke-width="0.8"/></svg>
          <span>+ 65 482 3316</span>
        </li>
        <li>
          <svg viewBox="0 0 10 10" aria-hidden="true"><rect x="0.5" y="2" width="9" height="6.5" fill="#7ab338"/><polyline points="0.5,2 5,5.8 9.5,2" fill="none" stroke="#3a3b3c" stroke-width="0.9"/></svg>
          <span>mlind@tavrenenergy.com</span>
        </li>
        <li>
          <svg viewBox="0 0 10 10" aria-hidden="true"><g fill="none" stroke="#7ab338" stroke-width="0.8"><circle cx="5" cy="5" r="4.4"/><ellipse cx="5" cy="5" rx="1.9" ry="4.4"/><line x1="0.6" y1="5" x2="9.4" y2="5"/><line x1="1.4" y1="2.8" x2="8.6" y2="2.8"/><line x1="1.4" y1="7.2" x2="8.6" y2="7.2"/></g></svg>
          <span>www.tavrenenergy.com</span>
        </li>
      </ul>
    </div>
    <div class="back-brand">
      <span class="brand-dot"></span>
      <span class="brand-name">Tavren Energy</span>
    </div>
  </section>
</main>
</body>
</html>
```